Business Cards for IT Consulting Company (Managed Service Provider)

I am looking to have some business cards printed and would like some designs. We are an IT Consulting company based in Vancouver BC. I would like a nice clean and modern look to the cards. I have uploaded all the versions of my logo so parts can be used as needed. Here is a snippit from our website homepage:

Quillbrook Networks Ltd. is an IT Solutions Partner located in Vancouver BC, Canada. We offer IT solutions and support to customers in the greater Vancouver Area. With expertise in Microsoft platforms, as well as Linux and Mac OSX and over 12 years experience in the IT industry, Quillbrook Networks is dedicated to offering our clients top quality service and products. We take pride in the solutions we offer our customers. The greatest compliment a client can give us is to recommend our services.

Quillbrook Networks Ltd. offers a wide range of IT services from onsite service to remote support and managed service solutions. This allows clients to choose the support path that best suits their company’s needs. Supporting many different sized companies from small to enterprise level over the past 12 years Quillbrook Networks has the experience and expertise needed to ensure things run smoothly. Allowing our clients to focus on doing business.

Revolutionizing the way IT services are delivered.

Quillbrook Networks is dedicated to providing our clients with IT solutions that work and grow with them for years to come. This philosophy helps save money in the long run instead of replacing equipment constantly. Far too often IT solutions are not well thought out and while possibly solving the problem at hand, require replacement due to growth or quality within a very short time frame. Quillbrook Networks takes pride in providing solutions that will last and be able to accommodate growth without the need for replacement.

Industry/Entity Type

Information Technology

Contact Information for Business Card

Quillbrook Networks Ltd.
(Employee Name)
Eml: (Employees Email Address)
Web: quillbrook.me
Ph: 604-555-0148

Font styles to use
Serif
Sans Serif

Requirements
Must have
• The Company logo and company colors.
Nice to have
• - Our tag line: "Revolutionizing IT Services" or "Revolutionizing the way IT services are delivered."
• - Also I really like the idea of nature and technology together blending which is sort of where my logo came from so integrating that somehow onto the business cards would be great.

```html
<!DOCTYPE html>
<html lang="en">
<head>
<meta charset="utf-8">
<title>Quillbrook Networks Ltd. — Business Cards</title>
<link rel="stylesheet" href="https://fonts.googleapis.com/css2?family=Source+Sans+3:wght@400;600;700&display=swap">
<style>
  :root {
    --backdrop: #3b3b3c;
    --card-grey: #5d5e60;
    --brand-blue: #1aa3dc;
    --paper: #ffffff;
    --ink: #555659;
    --pattern-tint: #e9f5fb;
  }
  * { box-sizing: border-box; margin: 0; padding: 0; }
  html, body {
    width: 1105px;
    height: 1200px;
    overflow: hidden;
    background: var(--backdrop);
    font-family: "Source Sans 3", "Helvetica Neue", Arial, sans-serif;
  }
  .card {
    position: absolute;
    left: 196px;
    width: 720px;
    height: 412px;
    overflow: hidden;
    background: var(--paper);
  }
  .card--front { top: 145px; background: var(--card-grey); }
  .card--back { top: 602px; }

  .front-shape { position: absolute; inset: 0; width: 720px; height: 412px; }

  .contact {
    position: absolute;
    left: 36px;
    top: 108px;
    color: var(--paper);
  }
  .contact__name {
    font-size: 31px;
    font-weight: 600;
    line-height: 1;
    margin-bottom: 26px;
  }
  .contact__address {
    font-size: 18.5px;
    line-height: 26px;
    margin-bottom: 8px;
  }
  .contact__list { list-style: none; }
  .contact__item {
    display: flex;
    align-items: center;
    font-size: 18.5px;
    line-height: 27.5px;
  }
  .contact__icon {
    width: 17px;
    height: 17px;
    margin-right: 10px;
    fill: var(--paper);
    flex: none;
  }

  .brand-name {
    position: absolute;
    left: 470px;
    top: 160px;
    width: 230px;
    color: var(--brand-blue);
    font-size: 34px;
    font-weight: 600;
    line-height: 1.05;
  }

  .back-pattern {
    position: absolute;
    inset: 0;
    background: var(--pattern-tint);
  }
  .back-brand {
    position: absolute;
    left: 0;
    right: 0;
    top: 172px;
    text-align: center;
    color: var(--brand-blue);
    font-size: 38px;
    font-weight: 600;
  }
  .tagline {
    position: absolute;
    left: 0;
    right: 0;
    top: 325px;
    text-align: center;
    color: var(--ink);
    font-size: 19.5px;
    font-weight: 700;
  }
</style>
</head>
<body>

<section class="card card--front" aria-label="Business card front">
  <svg class="front-shape" viewBox="0 0 720 412" aria-hidden="true">
    <polygon points="419,0 720,0 720,412 412,412 296,200" fill="var(--paper)"/>
    <polygon points="423,0 720,0 720,412 416,412 300,200" fill="var(--brand-blue)"/>
    <polygon points="440,21 720,21 720,391 437,391 326,200" fill="var(--paper)"/>
  </svg>

  <div class="contact">
    <p class="contact__name">Daniel Hartley</p>
    <p class="contact__address">4210 Fernwood Crescent<br>Vancouver, BC V5K 0A1</p>
    <ul class="contact__list">
      <li class="contact__item">
        <svg class="contact__icon" viewBox="0 0 24 24" aria-hidden="true"><path d="M6.6 10.8a15.1 15.1 0 0 0 6.6 6.6l2.2-2.2c.3-.3.7-.4 1-.2 1.1.4 2.3.6 3.6.6.6 0 1 .4 1 1V20c0 .6-.4 1-1 1A17 17 0 0 1 3 4c0-.6.4-1 1-1h3.5c.6 0 1 .4 1 1 0 1.3.2 2.5.6 3.6.1.3 0 .7-.2 1z"/></svg>
        604-555-0148
      </li>
      <li class="contact__item">
        <svg class="contact__icon" viewBox="0 0 24 24" aria-hidden="true"><path d="M2 5h20v14H2z M3.5 6.5 12 13l8.5-6.5" fill="none" stroke="#fff" stroke-width="2"/><path d="M2 5h20L12 12.5z"/></svg>
        dhartley@quillbrook.me
      </li>
      <li class="contact__item">
        <svg class="contact__icon" viewBox="0 0 24 24" aria-hidden="true"><circle cx="12" cy="12" r="10"/><path d="M7 8c2 0 3 1 3 2.5S8.5 12 8.5 14s1.5 2 1.5 4M15 5c-1 1.5 0 3 1.5 3S19 9.5 18 12s-2.5 2-2.5 4" fill="none" stroke="var(--card-grey)" stroke-width="1.6"/></svg>
        www.quillbrook.me
      </li>
    </ul>
  </div>

  <p class="brand-name">Quillbrook<br>Networks Ltd.</p>
</section>

<section class="card card--back" aria-label="Business card back">
  <div class="back-pattern" role="img" aria-label="Faint light-blue repeating hexagon pattern across the card"></div>
  <p class="back-brand">Quillbrook</p>
  <p class="tagline">Revolutionizing IT Services</p>
</section>

</body>
</html>
```